Modern HomePage Design for Church

We are looking for a modern homepage design using the sections we put together in the template. The colors we want are blue, black, grey, and white. We do not want use the colors in the logo. Please modify the logo color to match the website color scheme.

Target Market(s)

Church

Industry/Entity Type

Church

Number of Pages Required

1 page

Colors
0293ce
ffffff
474747
9d9d9d

```html
<!DOCTYPE html>
<html lang="en">
<head>
<meta charset="utf-8">
<title>Wellspring Grace Community Church</title>
<link href="https://fonts.googleapis.com/css2?family=Lato:wght@400;700;900&display=swap" rel="stylesheet">
<style>
:root{
  --blue:#0a3fc4;
  --blue-bright:#0293ce;
  --navy:#0d2560;
  --ink:#111111;
  --dark:#1b1b1b;
  --grey:#474747;
  --grey-light:#9d9d9d;
  --paper:#ffffff;
  --mist:#e9e9ea;
}
*{margin:0;padding:0;box-sizing:border-box}
html,body{width:1200px;height:4455px;overflow:hidden}
body{font-family:'Lato',sans-serif;color:var(--ink);background:var(--paper);position:relative}
section,header,footer{position:relative;width:1200px;overflow:hidden}
.btn{position:absolute;display:flex;align-items:center;justify-content:center;font-weight:900;font-size:13px;letter-spacing:.3px;text-transform:uppercase;white-space:nowrap}
.btn-outline-blue{border:2px solid var(--blue);color:var(--blue);background:var(--paper)}
.btn-blue{background:var(--blue);color:var(--paper)}
.btn-outline-white{border:2px solid var(--paper);color:var(--paper)}
.photo{position:absolute}

/* hero */
.hero{height:712px;background:linear-gradient(180deg,#2a1d14 0%,#5a3b22 40%,#7a4e2a 60%,#2b1d12 100%)}
.hero .photo{inset:0;background:radial-gradient(ellipse at 50% 65%,#c8874a 0%,#7a4d2b 30%,#2a1c12 75%)}
.hero::after{content:"";position:absolute;inset:0;background:rgba(0,0,0,.25)}
.nav{position:absolute;top:16px;left:0;width:1200px;display:flex;justify-content:center;gap:52px;z-index:2}
.nav a{color:var(--paper);font-size:14px;font-weight:700;text-decoration:none;text-transform:uppercase}
.brand{position:absolute;left:165px;top:92px;z-index:2;color:var(--paper);font-weight:400;display:flex;align-items:center;gap:10px}
.brand .mark{width:14px;height:14px;background:var(--paper);border-radius:50%}
.brand .name{font-size:30px;letter-spacing:1px;line-height:1}
.brand .sub{font-size:10px;letter-spacing:1.2px;margin-top:4px}
.hero-cta{z-index:2;top:85px;width:112px;height:30px;font-size:11px}
.hero-title{position:absolute;top:300px;width:1200px;text-align:center;color:var(--paper);z-index:2;text-transform:uppercase;font-weight:900}
.hero-title .l1{font-size:52px;line-height:1.1}
.hero-title .l2{font-size:33px;line-height:1.2}
.hero-main{left:500px;top:425px;width:200px;height:60px;font-size:17px;z-index:2}
.arrow{position:absolute;top:325px;width:50px;height:50px;border-radius:50%;background:rgba(120,120,120,.7);z-index:2;display:flex;align-items:center;justify-content:center}

.band{height:66px;background:var(--blue)}
.band p{position:absolute;left:225px;top:24px;color:var(--paper);font-weight:900;font-size:14px;text-transform:uppercase}
.band .btn{left:853px;top:13px;width:137px;height:40px;background:var(--ink);color:var(--paper);font-size:12px}

/* about */
.about{height:512px}
.about h2{position:absolute;left:170px;top:100px;font-size:34px;font-weight:900;text-transform:uppercase}
.about p{position:absolute;left:170px;width:450px;font-size:16px;line-height:1.6;color:var(--grey)}
.about .btn{left:170px;top:380px;width:166px;height:48px}
.about .photo{left:620px;top:0;width:345px;height:512px;background:linear-gradient(180deg,#ffffff 0%,#e9e6e2 30%,#2a2a2a 70%,#151515 100%)}

/* countdown */
.countdown{height:147px;background:var(--navy);color:var(--paper)}
.countdown .event{position:absolute;left:175px;top:48px;text-align:center}
.countdown .event b{display:block;font-size:17px;font-weight:900;text-transform:uppercase}
.countdown .event span{font-size:15px}
.units{position:absolute;left:575px;top:40px;display:flex}
.unit{width:90px;border-right:1px solid rgba(255,255,255,.35);padding-left:4px}
.unit:last-child{border-right:none}
.unit small{display:block;font-size:11px;font-weight:700;text-transform:uppercase}
.unit b{font-size:34px;font-weight:900;line-height:1.1}
.countdown .btn{left:935px;top:50px;width:143px;height:44px;font-size:12px}

/* features */
.features{height:463px;background:linear-gradient(180deg,#dfdfe1,#ececed 50%,#d6d6d8)}
.feature{position:absolute;top:70px;width:300px;text-align:center}
.feature svg{display:block;margin:0 auto 28px}
.feature h3{font-size:23px;font-weight:900;text-transform:uppercase;margin-bottom:14px}
.feature p{font-size:13px;line-height:1.6;color:var(--grey);width:240px;margin:0 auto}
.feature a{display:block;margin-top:22px;font-size:13px;font-weight:900;color:var(--ink);text-decoration:none;text-transform:uppercase}
.side-tab{position:absolute;right:20px;top:195px;width:50px;height:50px;background:#9d9d9d}

/* gallery */
.gallery{height:375px}
.tile{position:absolute}
.involved{position:absolute;left:735px;top:0;width:465px;height:375px;background:linear-gradient(180deg,#0a2b8c,#0b3fc0 60%,#05216b);color:var(--paper);text-align:center}
.involved h2,.blogs h2{font-size:24px;font-weight:900;text-transform:uppercase;margin-top:100px}
.involved p,.blogs p{font-size:15px;line-height:1.6;width:380px;margin:12px auto 0}

/* blogs & prayer */
.duo{height:375px}
.blogs{position:absolute;left:0;top:0;width:465px;height:375px;background:linear-gradient(135deg,#0b3fc0,#072b96);color:var(--paper);text-align:center}
.pray h2{position:absolute;left:535px;top:80px;font-size:30px;font-weight:900;text-transform:uppercase}
.pray p{position:absolute;left:535px;top:140px;width:480px;font-size:16px;line-height:1.6;color:var(--grey)}
.pray .btn{left:922px;top:285px;width:168px;height:50px}

/* pastor */
.ministry{height:457px;background:linear-gradient(90deg,#222 0%,#2c2c2c 50%,#1c1c1c 100%);color:var(--paper)}
.label{position:absolute;top:82px;font-size:15px;font-weight:900;text-transform:uppercase;display:flex;align-items:center;gap:10px}
.label::before{content:"";width:24px;height:2px;background:var(--paper)}
.pastor-photo{left:165px;top:143px;width:195px;height:225px;background:linear-gradient(135deg,#8a4a2a,#3a2a2a 60%,#6b5040)}
.pastor h3{position:absolute;left:385px;top:143px;width:280px;font-size:22px;font-weight:900;line-height:1.2}
.pastor p{position:absolute;left:385px;width:280px;font-size:13px;line-height:1.6;color:#d8d8d8}
.podcast{position:absolute;left:750px;width:300px;height:70px;border-bottom:1px solid rgba(255,255,255,.25)}
.podcast svg{position:absolute;left:0;top:8px}
.podcast b{position:absolute;left:72px;top:10px;font-size:15px;font-weight:700}
.podcast span{position:absolute;left:72px;top:34px;font-size:13px;color:#ccc}

/* events */
.events{height:933px}
.events h2{position:absolute;top:52px;width:1200px;text-align:center;color:var(--blue);font-size:32px;font-weight:900;text-transform:uppercase}
.event-row{position:absolute;left:0;width:1200px;height:200px}
.date{position:absolute;left:132px;top:0;width:86px;height:100px;background:var(--blue);color:var(--paper);text-align:center;padding-top:10px}
.date b{display:block;font-size:40px;font-weight:900;line-height:1}
.date span{font-size:14px;font-weight:900;text-transform:uppercase}
.event-photo{left:218px;top:0;width:285px;height:180px}
.event-row h3{position:absolute;left:538px;top:0;width:540px;font-size:21px;font-weight:900;line-height:1.2}
.meta{position:absolute;left:548px;font-size:13px;color:var(--grey);display:flex;align-items:center;gap:10px}
.event-row .btn{left:910px;top:60px;width:167px;height:50px}

/* footer */
.site-footer{height:343px;background:var(--ink);color:var(--paper)}
.site-footer h4{position:absolute;top:82px;font-size:16px;font-weight:900;text-transform:uppercase}
.post{position:absolute;width:260px;height:70px}
.post .thumb{position:absolute;left:0;top:0;width:90px;height:66px}
.post b{position:absolute;left:100px;top:0;font-size:13px;font-weight:900}
.post span{position:absolute;left:100px;top:20px;width:160px;font-size:12px;line-height:1.4;color:#bdbdbd}
.tags{position:absolute;left:492px;top:125px;width:245px;display:flex;flex-wrap:wrap;gap:9px}
.tags span{background:var(--blue);color:var(--paper);font-size:11px;font-weight:700;padding:6px 8px}
.copyright{position:relative;width:1200px;height:65px;background:#0a0a0a;color:#9d9d9d;font-size:11px;display:flex;align-items:center;justify-content:center}
</style>
</head>
<body>

<header class="hero">
  <div class="photo" role="img" aria-label="Cathedral nave interior with arches and a golden altar"></div>
  <nav class="nav">
    <a>Home</a><a>About Us</a><a>Services</a><a>Events</a><a>Blog</a><a>Why Us</a><a>Contact Us</a>
  </nav>
  <div class="brand">
    <div class="mark"></div>
    <div><div class="name">WELLSPRING</div><div class="sub">GRACE COMMUNITY CHURCH</div></div>
  </div>
  <div class="btn btn-blue hero-cta" style="left:758px">Learn More</div>
  <div class="btn btn-blue hero-cta" style="left:885px">Learn More</div>
  <div class="arrow" style="left:130px"><svg width="16" height="16" viewBox="0 0 16 16"><path d="M10 2 L4 8 L10 14" stroke="#fff" stroke-width="2.5" fill="none"/></svg></div>
  <div class="arrow" style="left:1012px"><svg width="16" height="16" viewBox="0 0 16 16"><path d="M6 2 L12 8 L6 14" stroke="#fff" stroke-width="2.5" fill="none"/></svg></div>
  <div class="hero-title"><div class="l1">Welcome to Wellspring</div><div class="l2">Grace Community Church</div></div>
  <div class="btn btn-blue hero-main">Learn More</div>
</header>

<section class="band">
  <p>Lorem ipsum dolor sit amet consectetuer adipiscing elit nam cursus</p>
  <div class="btn">Learn More</div>
</section>

<section class="about">
  <h2>About Wellspring</h2>
  <p style="top:150px">Pellentesque faucibus Ut accumsan ultricies elit Maecenas at justo id velit placerat molest</p>
  <p style="top:240px">Cras a ante vitae enim iaculis aliquam Mauris nunc quam venenatis nec euismod sit amet egestas placerat est Pellentesque habitant morbi tristique senectus et netus et malesuada fames ac turpis egestas Cras id e</p>
  <div class="btn btn-outline-blue">Learn More</div>
  <div class="photo" role="img" aria-label="Pastor in clerical clothing standing beside a smiling woman"></div>
</section>

<section class="countdown">
  <div class="event"><b>Pellentesque faucibus accumsan</b><span>MARCH 27, 2019 7:00 PM</span></div>
  <div class="units">
    <div class="unit"><small>Days</small><b>05</b></div>
    <div class="unit"><small>Hours</small><b>15</b></div>
    <div class="unit"><small>Minutes</small><b>28</b></div>
    <div class="unit"><small>Seconds</small><b>18</b></div>
  </div>
  <div class="btn btn-outline-white">Learn More</div>
</section>

<section class="features" role="img" aria-label="Soft faded photo of a person walking down a church aisle">
  <div class="feature" style="left:127px">
    <svg width="90" height="80" viewBox="0 0 90 80"><path d="M45 72 C20 52 8 40 8 24 C8 12 18 6 27 6 C36 6 42 12 45 18 C48 12 54 6 63 6 C72 6 82 12 82 24 C82 40 70 52 45 72Z" fill="none" stroke="#0a3fc4" stroke-width="3"/></svg>
    <h3>What We Believe</h3>
    <p>Pellentesque faucibus Ut accumsan ultricies elit Maecenas at justo id velit placerat molestie Donec dictum lectus non odio.</p>
    <a>Read More</a>
  </div>
  <div class="feature" style="left:445px">
    <svg width="90" height="80" viewBox="0 0 90 80"><path d="M35 70 C22 52 16 42 16 32 A19 19 0 0 1 54 32 C54 42 48 52 35 70Z" fill="none" stroke="#0a3fc4" stroke-width="3"/><circle cx="35" cy="32" r="7" fill="none" stroke="#0a3fc4" stroke-width="3"/><path d="M62 40 C54 28 52 24 52 18 A10 10 0 0 1 72 18 C72 24 70 28 62 40Z" fill="none" stroke="#0a3fc4" stroke-width="3"/><path d="M10 74 H80" stroke="#0a3fc4" stroke-width="3"/></svg>
    <h3>Services &amp; Location</h3>
    <p>Pellentesque faucibus Ut accumsan ultricies elit Maecenas at justo id velit placerat molestie Donec dictum lectus non odio.</p>
    <a>Read More</a>
  </div>
  <div class="feature" style="left:775px">
    <svg width="90" height="80" viewBox="0 0 90 80"><path d="M22 8 H68 V44 C68 58 56 66 45 72 C34 66 22 58 22 44Z" fill="none" stroke="#0a3fc4" stroke-width="3"/><path d="M34 34 C34 28 44 26 45 32 C46 26 56 28 56 34 C56 40 45 48 45 48 C45 48 34 40 34 34Z" fill="none" stroke="#0a3fc4" stroke-width="3"/></svg>
    <h3>Giving</h3>
    <p>Pellentesque faucibus Ut accumsan ultricies elit Maecenas at justo id velit placerat molestie Donec dictum lectus non odio.</p>
    <a>Read More</a>
  </div>
  <div class="side-tab"></div>
</section>

<section class="gallery">
  <div class="tile" style="left:0;top:0;width:365px;height:160px;background:linear-gradient(135deg,#bbb,#555)" role="img" aria-label="Crucifix in black and white"></div>
  <div class="tile" style="left:370px;top:0;width:180px;height:215px;background:linear-gradient(180deg,#1d2a4a,#b46a2a)" role="img" aria-label="Small chapel glowing at dusk"></div>
  <div class="tile" style="left:555px;top:0;width:180px;height:215px;background:linear-gradient(135deg,#5a1e10,#e0872c)" role="img" aria-label="Candles lit by hands"></div>
  <div class="tile" style="left:0;top:165px;width:180px;height:210px;background:linear-gradient(180deg,#6f9dd8,#6a4a34)" role="img" aria-label="Church spire against blue sky"></div>
  <div class="tile" style="left:185px;top:165px;width:180px;height:210px;background:linear-gradient(135deg,#8a7560,#2f2620)" role="img" aria-label="Hands holding a worn bible"></div>
  <div class="tile" style="left:370px;top:220px;width:365px;height:155px;background:linear-gradient(180deg,#3a2414,#b07a3a)" role="img" aria-label="Ornate church sanctuary interior"></div>
  <div class="involved" role="img" aria-label="Blue-toned church steeple silhouette">
    <h2>Get Involved</h2>
    <p>Pellentesque faucibus Ut accumsan ultricies elit Maecenas at justo id velit placerat molestie Donec dictum lectus</p>
  </div>
</section>

<section class="duo">
  <div class="blogs" role="img" aria-label="Blue-toned photo of an open book">
    <h2>Our Blogs</h2>
    <p>Pellentesque faucibus Ut accumsan ultricies elit Maecenas at justo id velit placerat molestie Donec dictum lectus</p>
  </div>
  <div class="pray">
    <h2>Pray Without Ceasing</h2>
    <p>Cras a ante vitae enim iaculis aliquam Mauris nunc quam venenatis nec euismod sit amet egestas placerat est Pellentesque habitant morbi tristique senectus et netus et malesuada fames ac turpis</p>
    <div class="btn btn-outline-blue">Learn More</div>
  </div>
</section>

<section class="ministry" role="img" aria-label="Dark photo of hands folded in prayer">
  <div class="label" style="left:165px">Pastor</div>
  <div class="photo pastor-photo" role="img" aria-label="Congregation members praying together"></div>
  <div class="pastor">
    <h3>Pellentesque faucibus Ut accumsan ultricies elit</h3>
    <p style="top:218px">Pellentesque faucibus Ut accumsan ultricies elit Maecenas at justo id velit placerat molestie</p>
    <p style="top:265px">Donec dictum lectus non odio Cras a ante vitae enim iaculis aliquam Mauris nunc quam venenatis nec euismod sit amet egestas place</p>
  </div>
  <div class="label" style="left:750px">Podcast</div>
  <div class="podcast" style="top:135px"><svg width="52" height="52" viewBox="0 0 52 52"><circle cx="26" cy="26" r="24" fill="none" stroke="#fff" stroke-width="2"/><path d="M21 17 L35 26 L21 35Z" fill="none" stroke="#fff" stroke-width="2"/></svg><b>Pellentesque faucibus</b><span>By Author Name</span></div>
  <div class="podcast" style="top:220px"><svg width="52" height="52" viewBox="0 0 52 52"><circle cx="26" cy="26" r="24" fill="none" stroke="#fff" stroke-width="2"/><path d="M21 17 L35 26 L21 35Z" fill="none" stroke="#fff" stroke-width="2"/></svg><b>Nunc tempus felis vitae</b><span>By Author Name</span></div>
  <div class="podcast" style="top:305px;border:none"><svg width="52" height="52" viewBox="0 0 52 52"><circle cx="26" cy="26" r="24" fill="none" stroke="#fff" stroke-width="2"/><path d="M21 17 L35 26 L21 35Z" fill="none" stroke="#fff" stroke-width="2"/></svg><b>Donec convallis pede venenat</b><span>By Author Name</span></div>
</section>

<section class="events">
  <h2>Upcoming Events</h2>

  <div class="event-row" style="top:150px">
    <div class="date"><b>10</b><span>Feb 18</span></div>
    <div class="photo event-photo" style="background:linear-gradient(135deg,#c98a52,#6a3a2a 60%,#d8b080)" role="img" aria-label="Congregation seated in pews"></div>
    <h3>Pellentesque faucibus Ut accumsan<br>ultricies elit Maecenas at just</h3>
    <div class="meta" style="top:75px"><svg width="14" height="14" viewBox="0 0 14 14"><rect x="1" y="2" width="12" height="11" fill="none" stroke="#0a3fc4" stroke-width="1.6"/><path d="M1 5 H13" stroke="#0a3fc4" stroke-width="1.6"/></svg>Thursday, 8:00 am - Thursday, 9:00 am -</div>
    <div class="meta" style="top:101px"><svg width="14" height="14" viewBox="0 0 14 14"><path d="M7 13 C4 9 2.5 7 2.5 5 A4.5 4.5 0 0 1 11.5 5 C11.5 7 10 9 7 13Z" fill="#0a3fc4"/></svg>St. Cedar Hill Chapel</div>
    <div class="meta" style="top:127px"><svg width="14" height="14" viewBox="0 0 14 14"><path d="M13 1 L1 6 L6 8 L8 13Z" fill="#0a3fc4"/></svg>Elm Lane, Riverton, United States, 10042</div>
    <div class="btn btn-outline-blue">Learn More</div>
  </div>

  <div class="event-row" style="top:400px">
    <div class="date"><b>08</b><span>Feb 18</span></div>
    <div class="photo event-photo" style="background:linear-gradient(135deg,#2a2a3a,#8a5a4a 50%,#2a2020)" role="img" aria-label="Hands clasped around a rosary"></div>
    <h3>Maecenas at justo id velit placerat molestie<br>Donec dictum lectus non odio Cras</h3>
    <div class="meta" style="top:75px"><svg width="14" height="14" viewBox="0 0 14 14"><rect x="1" y="2" width="12" height="11" fill="none" stroke="#0a3fc4" stroke-width="1.6"/><path d="M1 5 H13" stroke="#0a3fc4" stroke-width="1.6"/></svg>Thursday, 8:00 am - Thursday, 9:00 am -</div>
    <div class="meta" style="top:101px"><svg width="14" height="14" viewBox="0 0 14 14"><path d="M7 13 C4 9 2.5 7 2.5 5 A4.5 4.5 0 0 1 11.5 5 C11.5 7 10 9 7 13Z" fill="#0a3fc4"/></svg>St. Cedar Hill Chapel</div>
    <div class="meta" style="top:127px"><svg width="14" height="14" viewBox="0 0 14 14"><path d="M13 1 L1 6 L6 8 L8 13Z" fill="#0a3fc4"/></svg>Elm Lane, Riverton, United States, 10042</div>
    <div class="btn btn-outline-blue">Learn More</div>
  </div>

  <div class="event-row" style="top:665px">
    <div class="date"><b>05</b><span>Feb 18</span></div>
    <div class="photo event-photo" style="background:linear-gradient(135deg,#f2c25a,#c04a6a 50%,#5a2a6a)" role="img" aria-label="Glowing cross with warm bokeh light"></div>
    <h3>Duis non nunc Nulla rhoncus dictum metus<br>Curabitur tristique mi condimentum</h3>
    <div class="meta" style="top:75px"><svg width="14" height="14" viewBox="0 0 14 14"><rect x="1" y="2" width="12" height="11" fill="none" stroke="#0a3fc4" stroke-width="1.6"/><path d="M1 5 H13" stroke="#0a3fc4" stroke-width="1.6"/></svg>Thursday, 8:00 am - Thursday, 9:00 am -</div>
    <div class="meta" style="top:101px"><svg width="14" height="14" viewBox="0 0 14 14"><path d="M7 13 C4 9 2.5 7 2.5 5 A4.5 4.5 0 0 1 11.5 5 C11.5 7 10 9 7 13Z" fill="#0a3fc4"/></svg>St. Cedar Hill Chapel</div>
    <div class="meta" style="top:127px"><svg width="14" height="14" viewBox="0 0 14 14"><path d="M13 1 L1 6 L6 8 L8 13Z" fill="#0a3fc4"/></svg>Elm Lane, Riverton, United States, 10042</div>
    <div class="btn btn-outline-blue">Learn More</div>
  </div>
</section>

<footer class="site-footer">
  <h4 style="left:160px">Latest Blogs</h4>
  <div class="post" style="left:160px;top:125px"><div class="thumb" style="background:linear-gradient(135deg,#3a2414,#b07a3a)" role="img" aria-label="Church interior"></div><b>Maecenas at justo velit</b><span>placerat molestie Donec dictum lectus non odio Cras</span></div>
  <div class="post" style="left:160px;top:215px"><div class="thumb" style="background:linear-gradient(135deg,#3a2414,#b07a3a)" role="img" aria-label="Church interior"></div><b>Maecenas at justo velit</b><span>placerat molestie Donec dictum lectus non odio Cras</span></div>
  <h4 style="left:492px">Tags</h4>
  <div class="tags"><span>Donec</span><span>Dictum lectus</span><span>Lectus</span><span>Conubia</span><span>Lectus</span><span>Fusce ultricies</span><span>Dictum lectus</span></div>
  <h4 style="left:778px">Latest News</h4>
  <div class="post" style="left:778px;top:125px"><div class="thumb" style="background:linear-gradient(135deg,#e8d0b8,#7a5a4a)" role="img" aria-label="Chapel interior"></div><b>Maecenas at justo velit</b><span>placerat molestie Donec dictum lectus non odio Cras</span></div>
  <div class="post" style="left:778px;top:215px"><div class="thumb" style="background:linear-gradient(135deg,#e8d0b8,#7a5a4a)" role="img" aria-label="Chapel interior"></div><b>Maecenas at justo velit</b><span>placerat molestie Donec dictum lectus non odio Cras</span></div>
</footer>

<div class="copyright">© 2019 Company Name. All right reserved</div>

</body>
</html>
```